I have a logo and need to design the business card and stationery.
Updates

The uploaded logo image named as GREYMARSH CONSTRUCTION which is to be replaced to GREYMARSH CONTRACTS. Kindly add below details and submit the designs- Company name- Greymarsh Engineering Contracts LLP Name & Post- Kelvan Joshi (Designated Partner) Address- Block No.317, Wing C, Tulvo Trade Court, Manek Pural Road, Ruparel Industrial Estate, Goregaon(E), Mumbai - 400 063 Contact- +91 97415 60382 Email- kelvanjoshi@mailbrook.example Website- www.greymarshcontracts.example Contact for Letterhead- +91-22-28754193

Hi Tovin Rahul, We are liking your Design #28860835. We have suggested some changes which are mentioned in feedback. Kindly revert with it asap to finalize this design.

Colors

Designer to choose colors to be used in the design.

```html
<!DOCTYPE html>
<html lang="en">
<head>
<meta charset="utf-8">
<title>Greymarsh Contracts – Business Card</title>
<link rel="stylesheet" href="https://fonts.googleapis.com/css2?family=Montserrat:wght@400;500;600;700&display=swap">
<style>
  :root {
    --backdrop: #3b3b3b;
    --card-light: #ffffff;
    --card-dark: #313131;
    --ink: #2b2b2b;
    --ink-soft: #3a3a3a;
    --rule: #3a3a3a;
    --mark-dark: #1f1f1f;
  }
  html, body {
    margin: 0;
    padding: 0;
    width: 1200px;
    height: 1199px;
    overflow: hidden;
    background: var(--backdrop);
    font-family: "Montserrat", Arial, sans-serif;
  }
  .card {
    position: absolute;
    left: 237px;
    width: 726px;
    height: 414px;
    border-radius: 26px;
    box-sizing: border-box;
  }
  .card-front { top: 144px; background: var(--card-light); color: var(--ink); }
  .card-back  { top: 646px; background: var(--card-dark); }

  .brand {
    position: absolute;
    display: flex;
    flex-direction: column;
    align-items: center;
    font-weight: 700;
  }
  .brand-square { background: currentColor; }
  .brand-name {
    font-size: 30px;
    letter-spacing: 1px;
    line-height: 1;
    white-space: nowrap;
  }
  .brand-tag {
    font-size: 15px;
    letter-spacing: 13px;
    margin-right: -13px;
    line-height: 1;
    white-space: nowrap;
  }

  .card-front .brand { left: 46px; top: 138px; width: 305px; color: var(--ink); }
  .card-front .brand-square { width: 60px; height: 60px; margin-bottom: 24px; }
  .card-front .brand-tag { margin-top: 9px; }

  .divider {
    position: absolute;
    left: 384px;
    top: 92px;
    width: 1.5px;
    height: 232px;
    background: var(--rule);
  }

  .contact { position: absolute; left: 412px; top: 88px; width: 290px; color: var(--ink-soft); }
  .contact-name { margin: 0; font-size: 26px; font-weight: 600; letter-spacing: 0.6px; color: var(--ink); line-height: 1; }
  .contact-role { margin: 7px 0 0; font-size: 15px; font-weight: 400; letter-spacing: 1px; line-height: 1; }
  .contact-address { margin: 15px 0 0; font-size: 14px; font-style: normal; line-height: 20px; letter-spacing: 0.2px; }
  .contact-list { list-style: none; margin: 9px 0 0; padding: 0; font-size: 15px; line-height: 22px; letter-spacing: 0.2px; }
  .contact-list li { display: flex; align-items: center; gap: 6px; white-space: nowrap; }
  .contact-list svg { width: 12px; height: 12px; flex: none; }

  .card-back .brand { left: 0; right: 0; top: 105px; color: var(--mark-dark); }
  .card-back .brand-square { width: 124px; height: 124px; margin-bottom: 38px; }
  .card-back .brand-name { font-size: 38px; letter-spacing: 1.5px; }
  .card-back .brand-tag { font-size: 19px; letter-spacing: 16.5px; margin-right: -16.5px; margin-top: 10px; }
</style>
</head>
<body>
  <section class="card card-front" aria-label="Business card front">
    <div class="brand">
      <div class="brand-square" aria-hidden="true"></div>
      <div class="brand-name">GREYMARSH</div>
      <div class="brand-tag">CONTRACTS</div>
    </div>
    <div class="divider" aria-hidden="true"></div>
    <div class="contact">
      <h1 class="contact-name">KELVAN JOSHI</h1>
      <p class="contact-role">DESIGNATED PARTNER</p>
      <address class="contact-address">Block No.317, Wing C, Tulvo Trade Court,<br>Manek Pural Road, Ruparel Industrial<br>Estate, Goregaon(E), Mumbai - 400 063</address>
      <ul class="contact-list">
        <li>
          <svg viewBox="0 0 12 12" aria-hidden="true"><path d="M3 1.2 4.6 3.6 3.7 4.6C4.3 6 5.6 7.4 7 8.1L8 7.2 10.5 8.8 9.6 10.6C5.6 10.2 1.8 6.3 1.4 2.2Z" fill="none" stroke="#3a3a3a" stroke-width="1.2" stroke-linejoin="round"/></svg>
          <span>+91 97415 60382</span>
        </li>
        <li>
          <svg viewBox="0 0 12 12" aria-hidden="true"><rect x="1" y="2.5" width="10" height="7" fill="none" stroke="#3a3a3a" stroke-width="1.1"/><path d="M1 2.8 6 6.6 11 2.8" fill="none" stroke="#3a3a3a" stroke-width="1.1"/></svg>
          <span>kelvanjoshi@mailbrook.example</span>
        </li>
        <li>
          <svg viewBox="0 0 12 12" aria-hidden="true"><circle cx="6" cy="6" r="5" fill="none" stroke="#3a3a3a" stroke-width="1"/><ellipse cx="6" cy="6" rx="2.2" ry="5" fill="none" stroke="#3a3a3a" stroke-width="0.9"/><path d="M1 6H11M1.8 3.5H10.2M1.8 8.5H10.2" stroke="#3a3a3a" stroke-width="0.9"/></svg>
          <span>www.greymarshcontracts.example</span>
        </li>
      </ul>
    </div>
  </section>

  <section class="card card-back" aria-label="Business card back">
    <div class="brand">
      <div class="brand-square" aria-hidden="true"></div>
      <div class="brand-name">GREYMARSH</div>
      <div class="brand-tag">CONTRACTS</div>
    </div>
  </section>
</body>
</html>
```